Updated Business Card Re-design (Logo Provided)

I am needing to update our business cards for our practice, Brightfield Care Partners. We are a personal injury and wellness practice. The final design should be elegant and classy, but a type of card people would want to keep. Any samples should only have Dr. Tomas Verlinde on the template.
Updates

Went on vacation/holiday

Need extra days to review

Target Market(s)

Personal Injury clients, wellness clients

Industry/Entity Type

Personal Injury, medical, wellness

Contact Information for Business Card

dr and practice name, offerings

Requirements
Must have
• Single sided, this will be printed on a transparent business card, no exceptions.

```html
<!DOCTYPE html>
<html lang="en">
<head>
<meta charset="utf-8">
<title>Brightfield Care Partners – Business Card</title>
<link href="https://fonts.googleapis.com/css2?family=Lato:wght@400;700;900&family=Oswald:wght@500&display=swap" rel="stylesheet">
<style>
  :root {
    --page-bg: #e9e6e2;
    --card-top: #f4f5f6;
    --card-top-edge: #e4e6e9;
    --brand-blue: #1565ad;
    --band-blue: #1a6db5;
    --band-blue-light: #2f86c8;
    --accent-orange: #ea8c2c;
    --accent-green: #2f8a45;
    --name-grey: #a9b6c2;
    --specialty-tan: #ead6b8;
    --contact-white: #ffffff;
  }
  * { margin: 0; padding: 0; box-sizing: border-box; }
  html, body { width: 1200px; height: 900px; overflow: hidden; }
  body {
    background: var(--page-bg);
    display: flex; align-items: center; justify-content: center;
    font-family: "Lato", sans-serif;
  }
  .business-card {
    position: relative;
    width: 900px; height: 516px;
    border-radius: 22px;
    overflow: hidden;
    background: linear-gradient(180deg, var(--card-top), var(--card-top-edge));
    box-shadow: 0 10px 30px rgba(0,0,0,0.12);
  }
  .card-waves { position: absolute; inset: 0; width: 100%; height: 100%; }
  .brand {
    position: absolute; left: 130px; top: 88px;
    display: flex; align-items: center; gap: 18px;
  }
  .brand-dot {
    width: 40px; height: 40px; border-radius: 50%;
    background: var(--accent-orange);
  }
  .brand-name {
    font-family: "Lato", sans-serif; font-weight: 900;
    font-size: 42px; color: var(--brand-blue);
    text-transform: uppercase; letter-spacing: -0.5px;
  }
  .practitioner {
    position: absolute; right: 450px; top: 352px; text-align: right;
  }
  .practitioner-name {
    font-family: "Oswald", sans-serif; font-weight: 500;
    font-size: 31px; color: var(--name-grey); letter-spacing: 0.5px;
    text-transform: uppercase; white-space: nowrap;
  }
  .practitioner-specialty {
    font-weight: 700; font-size: 19px; color: var(--specialty-tan);
    margin-top: 4px;
  }
  .contact-list {
    position: absolute; left: 532px; top: 296px;
    list-style: none; color: var(--contact-white); font-size: 20px;
  }
  .contact-item { display: flex; align-items: flex-start; gap: 12px; line-height: 31px; }
  .contact-item.address { margin-bottom: 6px; }
  .contact-icon { width: 16px; height: 16px; margin-top: 8px; flex: none; fill: var(--contact-white); }
</style>
</head>
<body>
  <div class="business-card">
    <svg class="card-waves" viewBox="0 0 900 516" preserveAspectRatio="none" aria-hidden="true">
      <defs>
        <linearGradient id="bandGradient" x1="0" y1="1" x2="1" y2="0">
          <stop offset="0" stop-color="var(--band-blue-light)"/>
          <stop offset="1" stop-color="var(--band-blue)"/>
        </linearGradient>
      </defs>
      <path d="M0,172 C110,232 250,272 380,280 C260,264 120,224 0,150 Z" fill="var(--accent-orange)"/>
      <path d="M0,200 C150,252 280,284 390,282 C560,278 700,226 900,240 L900,516 L0,516 Z" fill="url(#bandGradient)"/>
      <path d="M530,236 C650,214 780,205 900,212 L900,232 C780,220 660,224 530,236 Z" fill="var(--accent-green)"/>
      <path d="M0,200 C150,252 280,284 390,282 C560,278 700,226 900,240" fill="none" stroke="#ffffff" stroke-width="5"/>
    </svg>

    <div class="brand">
      <span class="brand-dot"></span>
      <span class="brand-name">Brightfield Care Partners</span>
    </div>

    <div class="practitioner">
      <p class="practitioner-name">Dr. Tomas Verlinde, D.C.</p>
      <p class="practitioner-specialty">Medical-PT-Chiropractic</p>
    </div>

    <ul class="contact-list">
      <li class="contact-item address">
        <svg class="contact-icon" viewBox="0 0 16 16"><path d="M8 0a5.5 5.5 0 0 0-5.5 5.5C2.5 10 8 16 8 16s5.5-6 5.5-10.5A5.5 5.5 0 0 0 8 0zm0 8a2.5 2.5 0 1 1 0-5 2.5 2.5 0 0 1 0 5z"/></svg>
        <span>4820 Orchard Ridge Road, Suite 12<br>Marlow Falls, GA 30999</span>
      </li>
      <li class="contact-item">
        <svg class="contact-icon" viewBox="0 0 16 16"><path d="M3.6 1l2.4 3-1.3 1.8a9 9 0 0 0 5.5 5.5L12 10l3 2.4-1.4 2.6C7.5 15 1 8.5 1 2.4z"/></svg>
        <span>555.214.0387</span>
      </li>
      <li class="contact-item">
        <svg class="contact-icon" viewBox="0 0 16 16"><path d="M4 0h8a1.5 1.5 0 0 1 1.5 1.5v13A1.5 1.5 0 0 1 12 16H4a1.5 1.5 0 0 1-1.5-1.5v-13A1.5 1.5 0 0 1 4 0zm0 2v10h8V2zm4 11a1 1 0 1 0 0 2 1 1 0 0 0 0-2z"/></svg>
        <span>555.318.6642</span>
      </li>
      <li class="contact-item">
        <svg class="contact-icon" viewBox="0 0 16 16"><path d="M1 3h14v1.2L8 9 1 4.2zm0 2.6l7 4.8 7-4.8V13H1z"/></svg>
        <span>hello@brightfieldcare.com</span>
      </li>
      <li class="contact-item">
        <svg class="contact-icon" viewBox="0 0 16 16"><path d="M8 0a8 8 0 1 0 0 16A8 8 0 0 0 8 0zm5.9 7h-2.5a12 12 0 0 0-1-4.6A6 6 0 0 1 13.9 7zM8 2c.8 1 1.4 2.9 1.5 5h-3C6.6 4.9 7.2 3 8 2zM5.6 2.4A12 12 0 0 0 4.6 7H2.1a6 6 0 0 1 3.5-4.6zM2.1 9h2.5a12 12 0 0 0 1 4.6A6 6 0 0 1 2.1 9zM8 14c-.8-1-1.4-2.9-1.5-5h3c-.1 2.1-.7 4-1.5 5zm2.4-.4a12 12 0 0 0 1-4.6h2.5a6 6 0 0 1-3.5 4.6z"/></svg>
        <span>brightfieldcare.com</span>
      </li>
    </ul>
  </div>
</body>
</html>
```